CrestHornSupply.com

I need a new webdesign for a company in the San Jose/SF Bay area that showcases the financial benefits of buying used band instruments for junior high students.This would be opposed to the current and costly option of renting cheap quality instruments from the 2 or 3 local music stores that charge a monthly fee that over the years charges the buyer 3 or 4x over..
Instruments: focus in on Alto Sax, Trumpet, Flute, Clarinet, Trombone, Tenor Sax, Baritone
Target middle schools are Larkfield Middle School and Maple Middle School in San Jose, CA. Both have award winning band programs.
Files attached may or may not be important.
Tabs Needed and funtional
Contact
Shopping Cart
Select Instrument
Checkout
Add to Cart, etc.
Instuments
quantity, etc.
trade in your instrument/sell your instrument
ability to add or take away new instruments for sale. including pictures
Additional questions or info, feel free to ask
Updates
Hi Designers,
Project Deadline Extended
Reason: In the next week you will be receiving specific content that will be required to be had on the website.
New desigins are still welcome. Please continue to contact me if you have questions about your individual designs.
Thanks!
Crest Horn

```html
<!DOCTYPE html>
<html lang="en">
<head>
<meta charset="utf-8">
<title>Crest Horn Instruments – Musical Instruments</title>
<link href="https://fonts.googleapis.com/css2?family=Open+Sans:wght@400;600;700&display=swap" rel="stylesheet">
<style>
:root{
  --yellow:#f5c13b;
  --yellow-dark:#c99a1f;
  --ink:#333333;
  --ink-soft:#555555;
  --rule:#dcdcdc;
  --card-border:#d6d6d6;
  --backdrop:#ececec;
  --page:#ffffff;
  --link:#1aa3c9;
  --red:#e0312b;
}
*{box-sizing:border-box;margin:0;padding:0}
html,body{width:1154px;height:1200px;overflow:hidden}
body{background:var(--backdrop);font-family:"Open Sans",Arial,sans-serif;color:var(--ink);position:relative}
.page{position:absolute;left:175px;top:0;width:804px;height:1152px;background:var(--page);box-shadow:0 0 6px rgba(0,0,0,.12)}
.abs{position:absolute}

/* header */
.account-links{right:-5px;top:12px;font-size:8.5px;color:var(--ink)}
.brand{left:0;top:34px;display:flex;align-items:center;gap:6px}
.brand-dot{width:14px;height:14px;border-radius:50%;background:var(--yellow)}
.brand-name{font-size:26px;font-weight:700;color:var(--ink);letter-spacing:.5px}
.promo{background:var(--yellow);border-radius:5px;font-size:9.5px;font-weight:600;color:var(--ink);height:22px;display:flex;align-items:center;gap:6px;padding:0 8px}
.promo svg{width:11px;height:11px}
.search{left:433px;top:66px;width:216px;height:23px;border:1px solid var(--rule);border-radius:12px;font-size:7.5px;color:#999;display:flex;align-items:center;padding-left:12px}
.search-btn{position:absolute;right:-1px;top:-1px;width:28px;height:23px;background:var(--yellow);border-radius:0 8px 8px 0;display:flex;align-items:center;justify-content:center}
.cart{left:677px;top:69px;font-size:12px;color:var(--ink-soft);display:flex;align-items:center;gap:5px}
.cart .count{color:var(--red)}
.bag-btn{left:752px;top:66px;width:59px;height:23px;background:var(--yellow);border-radius:5px;font-size:9.5px;font-weight:600;display:flex;align-items:center;justify-content:center}

/* nav */
.nav{left:-6px;top:103px;width:817px;height:27px;background:var(--yellow);display:flex;align-items:center}
.nav a{font-size:9.5px;color:var(--ink);text-decoration:none;padding:0 11px;height:27px;display:flex;align-items:center;border-right:1px solid var(--yellow-dark)}
.nav a:first-child{padding-left:14px}
.nav a:last-of-type{border-right:none}
.nav .social{margin-left:auto;display:flex;gap:8px;padding-right:14px}
.fold{top:130px;width:0;height:0;border-top:6px solid var(--yellow-dark)}
.fold.l{left:-6px;border-left:6px solid transparent}
.fold.r{left:805px;border-right:6px solid transparent}
.nav-shadow{left:0;top:130px;width:804px;height:7px;background:#e4e4e4}
.dot{width:11px;height:11px;border-radius:50%;background:var(--ink)}

/* breadcrumb */
.crumbs{left:17px;top:147px;font-size:8.5px;color:var(--ink)}
.crumb-rule{left:17px;top:167px;width:161px;height:1px;background:var(--rule)}

/* sidebar */
.filter{left:17px;width:161px;background:var(--yellow);border-radius:7px;padding:10px 14px;font-size:9.5px}
.filter h3{font-size:9.5px;font-weight:400;display:flex;align-items:center;gap:6px}
.tri-down{width:0;height:0;border-left:4.5px solid transparent;border-right:4.5px solid transparent;border-top:5px solid var(--ink)}
.tri-right{width:0;height:0;border-top:4.5px solid transparent;border-bottom:4.5px solid transparent;border-left:5px solid var(--ink);margin-left:3px}
.filter ul{list-style:none;margin:8px 0 0 9px}
.filter li{display:flex;align-items:center;gap:6px;line-height:12.5px}
.box{width:8px;height:8px;background:var(--ink);display:inline-flex;align-items:center;justify-content:center}
.slider{margin-top:9px;height:1px;background:var(--ink);position:relative}
.slider::after{content:"";position:absolute;left:58px;top:-2.5px;width:6px;height:6px;border-radius:50%;background:var(--ink)}
.range{display:flex;justify-content:space-between;margin-top:3px;font-size:9px}

/* listing */
.list-head{left:213px;top:168px;width:574px;height:29px;border-top:1px solid var(--rule);border-bottom:1px solid var(--rule);display:flex;align-items:center}
.list-title{font-size:12.5px;color:var(--ink)}
.records{font-size:8px;margin-left:98px}
.pager{margin-left:auto;display:flex;align-items:center;gap:5px;font-size:9.5px}
.pager .on{background:var(--ink);color:#fff;border-radius:3px;width:11px;height:13px;display:flex;align-items:center;justify-content:center}
.row-rule{left:213px;width:574px;height:1px;background:var(--rule)}
.card{width:132px}
.thumb{width:132px;height:132px;border:1px solid var(--card-border);border-radius:5px;background:linear-gradient(135deg,#ffffff 35%,#d9d9d9 50%,#ffffff 65%)}
.card .name{text-align:center;font-size:9.5px;margin-top:10px}
.card .price{text-align:center;font-size:12.5px;margin-top:0}
.list-foot{left:213px;top:983px;width:574px;display:flex;align-items:center}

/* footer */
.foot-rule{left:17px;top:1004px;width:770px;height:1px;background:var(--rule)}
.foot-social{left:0;width:804px;top:1024px;display:flex;justify-content:center;gap:10px}
.contact-line{left:0;width:804px;top:1048px;text-align:center;font-size:8.5px}
.contact-line a,.copy a{color:var(--link);text-decoration:none}
.pay{left:0;width:804px;top:1070px;display:flex;justify-content:center;gap:3px}
.pay span{width:24px;height:15px;border:1px solid #cfcfcf;border-radius:2px;background:#f0f0f0}
.pay span:nth-child(2){background:#e8a33a}.pay span:nth-child(3){background:#3a5aa8}.pay span:nth-child(4){background:#5b9bd5}.pay span:nth-child(5){background:#f7e7a0}
.foot-links{left:0;width:804px;top:1103px;text-align:center;font-size:8.5px;word-spacing:2px}
.foot-links b{font-weight:400;margin:0 7px}
.copy{left:0;width:804px;top:1124px;text-align:center;font-size:8.5px}
</style>
</head>
<body>
<div class="page">
  <div class="abs account-links">My account &nbsp;|&nbsp; My wishlist</div>
  <div class="abs brand"><span class="brand-dot"></span><span class="brand-name">CREST HORN</span></div>

  <div class="abs promo" style="left:224px;top:37px">
    <svg viewBox="0 0 12 12"><rect x="0" y="3" width="7" height="5" fill="#333"/><rect x="7" y="5" width="4" height="3" fill="#333"/><circle cx="3" cy="9.5" r="1.3" fill="#333"/><circle cx="9" cy="9.5" r="1.3" fill="#333"/></svg>
    FREE POSTAGE ON ORDERS OVER $50</div>
  <div class="abs promo" style="left:224px;top:66px">
    <svg viewBox="0 0 12 12"><rect x="1" y="4" width="10" height="7" fill="#333"/><rect x="5.3" y="1" width="1.4" height="10" fill="#f5c13b"/></svg>
    FREE GIFT WRAPPING</div>

  <div class="abs search">FIND A PRODUCT OR BRAND
    <span class="search-btn"><svg width="13" height="13" viewBox="0 0 13 13"><circle cx="5" cy="5" r="3.5" fill="none" stroke="#333" stroke-width="1.6"/><line x1="7.5" y1="7.5" x2="12" y2="12" stroke="#333" stroke-width="2"/></svg></span>
  </div>
  <div class="abs cart">
    <svg width="10" height="9" viewBox="0 0 10 9"><path d="M0 1h2l1.5 5h5l1-4H3" fill="none" stroke="#555" stroke-width="1.2"/><circle cx="4" cy="8" r="1" fill="#555"/><circle cx="8" cy="8" r="1" fill="#555"/></svg>
    $0.00 <span>(<span class="count">0</span>)</span></div>
  <div class="abs bag-btn">MY BAG</div>

  <nav class="abs nav">
    <a href="#">HOME</a><a href="#">ABOUT</a><a href="#">INSTUMENTS</a><a href="#">TRADE IN YOUR INSTRUMENT</a><a href="#">SELL YOUR INSTRUMENT</a><a href="#">FAQ'S</a><a href="#">CONTACT US</a>
    <span class="social"><span class="dot"></span><span class="dot"></span><span class="dot"></span></span>
  </nav>
  <div class="abs fold l"></div><div class="abs fold r"></div>
  <div class="abs nav-shadow"></div>

  <div class="abs crumbs">HOME &nbsp;&gt;&nbsp; EDUCATIONAL &nbsp;&gt;&nbsp; MUSICAL INSTRUMENTS</div>
  <div class="abs crumb-rule"></div>

  <aside>
    <div class="abs filter" style="top:179px;height:102px">
      <h3><span class="tri-down"></span>AGE GROUP</h3>
      <ul>
        <li><span class="box"></span>6-12 months (1)</li>
        <li><span class="box"><svg width="7" height="7" viewBox="0 0 7 7"><path d="M1 3.5l1.8 1.8L6 1.5" fill="none" stroke="#f5c13b" stroke-width="1.2"/></svg></span>12-18 months (5)</li>
        <li><span class="box"></span>2 years (9)</li>
        <li><span class="box"></span>3 years (5)</li>
      </ul>
    </div>
    <div class="abs filter" style="top:291px;height:34px"><h3><span class="tri-right"></span>GENDER</h3></div>
    <div class="abs filter" style="top:334px;height:34px"><h3><span class="tri-right"></span>BRAND</h3></div>
    <div class="abs filter" style="top:379px;height:62px">
      <h3><span class="tri-down"></span>PRICE</h3>
      <div class="slider"></div>
      <div class="range"><span>$0</span><span>$800</span></div>
    </div>
  </aside>

  <section>
    <div class="abs list-head">
      <span class="list-title">MUSICAL INSTRUMENTS</span>
      <span class="records">( 1 - 35 OF 461 RECORDS )</span>
      <span class="pager"><span>&lt;&lt;</span><span>&lt;</span><span>1</span><span>2</span><span>3</span><span>4</span><span>5</span><span>6</span><span class="on">7</span><span>8</span><span>9</span><span>10</span><span>&gt;</span><span>&gt;&gt;</span></span>
    </div>

    <!-- row 1 -->
    <div class="abs card" style="left:213px;top:212px"><div class="thumb" role="img" aria-label="Black clarinet photo"></div><div class="name">Clarinet</div><div class="price">$249.17</div></div>
    <div class="abs card" style="left:360px;top:212px"><div class="thumb" role="img" aria-label="Bass clarinet photo"></div><div class="name">Clarinet</div><div class="price">$249.17</div></div>
    <div class="abs card" style="left:509px;top:212px"><div class="thumb" role="img" aria-label="Bass clarinet photo"></div><div class="name">Clarinet</div><div class="price">$249.17</div></div>
    <div class="abs card" style="left:656px;top:212px"><div class="thumb" role="img" aria-label="Black clarinet photo"></div><div class="name">Clarinet</div><div class="price">$249.17</div></div>
    <div class="abs row-rule" style="top:393px"></div>
    <!-- row 2 -->
    <div class="abs card" style="left:213px;top:408px"><div class="thumb" role="img" aria-label="Black clarinet photo"></div><div class="name">Clarinet</div><div class="price">$249.17</div></div>
    <div class="abs card" style="left:360px;top:408px"><div class="thumb" role="img" aria-label="Bass clarinet photo"></div><div class="name">Clarinet</div><div class="price">$249.17</div></div>
    <div class="abs card" style="left:509px;top:408px"><div class="thumb" role="img" aria-label="Bass clarinet photo"></div><div class="name">Clarinet</div><div class="price">$249.17</div></div>
    <div class="abs card" style="left:656px;top:408px"><div class="thumb" role="img" aria-label="Black clarinet photo"></div><div class="name">Clarinet</div><div class="price">$249.17</div></div>
    <div class="abs row-rule" style="top:588px"></div>
    <!-- row 3 -->
    <div class="abs card" style="left:213px;top:602px"><div class="thumb" role="img" aria-label="Black clarinet photo"></div><div class="name">Clarinet</div><div class="price">$249.17</div></div>
    <div class="abs card" style="left:360px;top:602px"><div class="thumb" role="img" aria-label="Bass clarinet photo"></div><div class="name">Clarinet</div><div class="price">$249.17</div></div>
    <div class="abs card" style="left:509px;top:602px"><div class="thumb" role="img" aria-label="Bass clarinet photo"></div><div class="name">Clarinet</div><div class="price">$249.17</div></div>
    <div class="abs card" style="left:656px;top:602px"><div class="thumb" role="img" aria-label="Black clarinet photo"></div><div class="name">Clarinet</div><div class="price">$249.17</div></div>
    <div class="abs row-rule" style="top:782px"></div>
    <!-- row 4 -->
    <div class="abs card" style="left:213px;top:797px"><div class="thumb" role="img" aria-label="Black clarinet photo"></div><div class="name">Clarinet</div><div class="price">$249.17</div></div>
    <div class="abs card" style="left:360px;top:797px"><div class="thumb" role="img" aria-label="Bass clarinet photo"></div><div class="name">Clarinet</div><div class="price">$249.17</div></div>
    <div class="abs card" style="left:509px;top:797px"><div class="thumb" role="img" aria-label="Bass clarinet photo"></div><div class="name">Clarinet</div><div class="price">$249.17</div></div>
    <div class="abs card" style="left:656px;top:797px"><div class="thumb" role="img" aria-label="Black clarinet photo"></div><div class="name">Clarinet</div><div class="price">$249.17</div></div>
    <div class="abs row-rule" style="top:977px"></div>

    <div class="abs list-foot">
      <span class="records" style="margin-left:238px">( 1 - 35 OF 461 RECORDS )</span>
      <span class="pager"><span>&lt;&lt;</span><span>&lt;</span><span>1</span><span>2</span><span>3</span><span>4</span><span>5</span><span>6</span><span class="on">7</span><span>8</span><span>9</span><span>10</span><span>&gt;</span><span>&gt;&gt;</span></span>
    </div>
  </section>

  <footer>
    <div class="abs foot-rule"></div>
    <div class="abs foot-social"><span class="dot"></span><span class="dot"></span><span class="dot"></span></div>
    <div class="abs contact-line">Call 0198 7654 321 or email <a href="#">contact@cresthornsupply.com</a></div>
    <div class="abs pay"><span></span><span></span><span></span><span></span><span></span><span></span><span></span><span></span><span></span></div>
    <div class="abs foot-links">Home<b>|</b>About<b>|</b>Instuments<b>|</b>Trade in your instrument<b>|</b>Sell your instrument<b>|</b>FAQ's<b>|</b>Contact Us</div>
    <div class="abs copy">Copyright 2013 Crest Horn Instruments &nbsp;|&nbsp; Website Designed by <a href="#">fernlinestudio.com</a></div>
  </footer>
</div>
</body>
</html>
```